Brindlewick Solutions Ltd

I'd like to create a company letterhead for the attached logo in word format.

I'd like to emphasis the icon in large translucent state from the left corner and ensure that the letterhead colouring matches the colour palette of the current logo with a contrast so it's clear to see. I've attached a copy of our sister company page on the app for reference.

```html
<!DOCTYPE html>
<html lang="en">
<head>
<meta charset="utf-8">
<title>Brindlewick Solutions Ltd – Letterhead Set</title>
<link href="https://fonts.googleapis.com/css2?family=Lato:wght@400;700&family=Montserrat:wght@400&display=swap" rel="stylesheet">
<style>
  :root {
    --backdrop: #b5b5b5;
    --paper: #ffffff;
    --ink: #1c1c1c;
    --ink-soft: #3a3a3a;
    --teal: #10b9a6;
    --teal-glow: rgba(16, 185, 166, 0.13);
    --grey-glow: rgba(0, 0, 0, 0.06);
    --dark-band: #151515;
    --on-dark: #ffffff;
  }
  * { box-sizing: border-box; margin: 0; padding: 0; }
  html, body { width: 961px; height: 1200px; overflow: hidden; }
  body {
    background: var(--backdrop);
    font-family: "Lato", sans-serif;
    position: relative;
  }
  .icon-defs { position: absolute; width: 0; height: 0; }

  .sheet {
    position: absolute;
    width: 343px;
    height: 485px;
    background: var(--paper);
    overflow: hidden;
    color: var(--ink-soft);
  }
  .sheet--one   { left: 111px; top: 92px; }
  .sheet--two   { left: 490px; top: 92px; }
  .sheet--three { left: 111px; top: 612px; }
  .sheet--four  { left: 490px; top: 612px; }

  .header-band {
    position: absolute; left: 0; top: 0;
    width: 100%; height: 102px;
  }
  .sheet--dark .header-band { background: var(--dark-band); }

  .accent-bar {
    position: absolute; top: 0; left: 234px;
    width: 86px; height: 5px;
    background: var(--teal);
  }
  .sheet--two .accent-bar { background: #000; }
  .sheet--four .accent-bar { background: var(--on-dark); }

  .brand {
    position: absolute; left: 25px; top: 30px;
    width: 78px;
    display: flex; flex-direction: column; align-items: center;
    color: var(--teal);
  }
  .brand__dot {
    width: 24px; height: 24px;
    border-radius: 50%;
    background: currentColor;
    margin-bottom: 5px;
  }
  .brand__name {
    font-family: "Lato", sans-serif;
    font-weight: 400;
    font-size: 13px;
    line-height: 1;
    letter-spacing: 0.1px;
    white-space: nowrap;
  }
  .sheet--two .brand { color: #000; }
  .sheet--four .brand { color: var(--on-dark); }

  .contact {
    position: absolute; right: 26px; top: 27px;
    text-align: right;
    font-size: 5.6px;
    line-height: 7.5px;
    color: var(--ink-soft);
  }
  .contact__company { color: var(--teal); }
  .sheet--two .contact__company { color: var(--ink); }
  .sheet--dark .contact { color: var(--on-dark); }
  .sheet--four .contact__company { color: var(--on-dark); }
  .contact__address { margin-bottom: 4px; }
  .contact__line { display: flex; justify-content: flex-end; align-items: center; gap: 4px; }
  .contact__icon { width: 5px; height: 5px; fill: var(--teal); }
  .sheet--two .contact__icon { fill: #000; }
  .sheet--four .contact__icon { fill: var(--on-dark); }

  .backdrop-glow {
    position: absolute; left: 0; bottom: 0;
    width: 100%; height: 62%;
    background: radial-gradient(circle at 18% 77%, var(--teal-glow) 0%, var(--teal-glow) 22%, rgba(16,185,166,0.04) 48%, transparent 68%);
  }
  .sheet--two .backdrop-glow {
    background: radial-gradient(circle at 18% 77%, var(--grey-glow) 0%, var(--grey-glow) 22%, rgba(0,0,0,0.02) 48%, transparent 68%);
  }

  .caption {
    position: absolute;
    width: 343px;
    text-align: center;
    font-size: 8px;
    letter-spacing: 0.8px;
    color: var(--ink);
  }
  .caption--one   { left: 111px; top: 589px; }
  .caption--two   { left: 490px; top: 589px; }
  .caption--three { left: 111px; top: 1109px; }
  .caption--four  { left: 490px; top: 1109px; }
</style>
</head>
<body>

<svg class="icon-defs" aria-hidden="true">
  <defs>
    <symbol id="icon-phone" viewBox="0 0 10 10">
      <path d="M2 0.5 L3.8 2.6 L2.9 3.6 Q4 5.8 6.4 7.1 L7.4 6.2 L9.5 8 L8.3 9.5 Q4.5 9.3 2 6.5 Q0.3 4.3 0.5 1.7 Z"/>
    </symbol>
    <symbol id="icon-fax" viewBox="0 0 10 10">
      <path d="M2.5 0.5 H7.5 V3 H9.5 V7.5 H7.5 V9.5 H2.5 V7.5 H0.5 V3 H2.5 Z M3.5 1.5 V3 H6.5 V1.5 Z M3.5 6 V8.5 H6.5 V6 Z"/>
    </symbol>
    <symbol id="icon-mail" viewBox="0 0 10 10">
      <path d="M0.5 2 H9.5 V8 H0.5 Z M1.3 2.6 L5 5.4 L8.7 2.6 Z"/>
    </symbol>
    <symbol id="icon-web" viewBox="0 0 10 10">
      <circle cx="5" cy="5" r="4.5"/>
    </symbol>
  </defs>
</svg>

<!-- Letterhead 01 -->
<section class="sheet sheet--one">
  <div class="backdrop-glow" role="img" aria-label="Large translucent brand mark with soft rays from the lower left corner"></div>
  <div class="accent-bar"></div>
  <div class="brand"><span class="brand__dot"></span><span class="brand__name">Brindlewick</span></div>
  <address class="contact" style="font-style:normal">
    <div class="contact__company">Brindlewick Solutions Ltd</div>
    <div class="contact__address">4702 Harlow Lane<br>Ashford, CT 06278</div>
    <div class="contact__line">(555) 014-2286 <svg class="contact__icon"><use href="#icon-phone"/></svg></div>
    <div class="contact__line">(555) 014-2286 <svg class="contact__icon"><use href="#icon-fax"/></svg></div>
    <div class="contact__line">info@brindlewicksolutions.com <svg class="contact__icon"><use href="#icon-mail"/></svg></div>
    <div class="contact__line">brindlewicksolutions.com <svg class="contact__icon"><use href="#icon-web"/></svg></div>
  </address>
</section>
<div class="caption caption--one">LETERHEAD 01</div>

<!-- Letterhead 02 -->
<section class="sheet sheet--two">
  <div class="backdrop-glow" role="img" aria-label="Large translucent grey brand mark with soft rays from the lower left corner"></div>
  <div class="accent-bar"></div>
  <div class="brand"><span class="brand__dot"></span><span class="brand__name">Brindlewick</span></div>
  <address class="contact" style="font-style:normal">
    <div class="contact__company">Brindlewick Solutions Ltd</div>
    <div class="contact__address">4702 Harlow Lane<br>Ashford, CT 06278</div>
    <div class="contact__line">(555) 014-2286 <svg class="contact__icon"><use href="#icon-phone"/></svg></div>
    <div class="contact__line">(555) 014-2286 <svg class="contact__icon"><use href="#icon-fax"/></svg></div>
    <div class="contact__line">info@brindlewicksolutions.com <svg class="contact__icon"><use href="#icon-mail"/></svg></div>
    <div class="contact__line">brindlewicksolutions.com <svg class="contact__icon"><use href="#icon-web"/></svg></div>
  </address>
</section>
<div class="caption caption--two">LETERHEAD 02</div>

<!-- Letterhead 03 -->
<section class="sheet sheet--three sheet--dark">
  <div class="backdrop-glow" role="img" aria-label="Large translucent brand mark with soft rays from the lower left corner"></div>
  <div class="header-band"></div>
  <div class="accent-bar"></div>
  <div class="brand"><span class="brand__dot"></span><span class="brand__name">Brindlewick</span></div>
  <address class="contact" style="font-style:normal">
    <div class="contact__company">Brindlewick Solutions Ltd</div>
    <div class="contact__address">4702 Harlow Lane<br>Ashford, CT 06278</div>
    <div class="contact__line">(555) 014-2286 <svg class="contact__icon"><use href="#icon-phone"/></svg></div>
    <div class="contact__line">(555) 014-2286 <svg class="contact__icon"><use href="#icon-fax"/></svg></div>
    <div class="contact__line">info@brindlewicksolutions.com <svg class="contact__icon"><use href="#icon-mail"/></svg></div>
    <div class="contact__line">brindlewicksolutions.com <svg class="contact__icon"><use href="#icon-web"/></svg></div>
  </address>
</section>
<div class="caption caption--three">LETERHEAD 03</div>

<!-- Letterhead 04 -->
<section class="sheet sheet--four sheet--dark">
  <div class="backdrop-glow" role="img" aria-label="Large translucent brand mark with soft rays from the lower left corner"></div>
  <div class="header-band"></div>
  <div class="accent-bar"></div>
  <div class="brand"><span class="brand__dot"></span><span class="brand__name">Brindlewick</span></div>
  <address class="contact" style="font-style:normal">
    <div class="contact__company">Brindlewick Solutions Ltd</div>
    <div class="contact__address">4702 Harlow Lane<br>Ashford, CT 06278</div>
    <div class="contact__line">(555) 014-2286 <svg class="contact__icon"><use href="#icon-phone"/></svg></div>
    <div class="contact__line">(555) 014-2286 <svg class="contact__icon"><use href="#icon-fax"/></svg></div>
    <div class="contact__line">info@brindlewicksolutions.com <svg class="contact__icon"><use href="#icon-mail"/></svg></div>
    <div class="contact__line">brindlewicksolutions.com <svg class="contact__icon"><use href="#icon-web"/></svg></div>
  </address>
</section>
<div class="caption caption--four">LETERHEAD 04</div>

</body>
</html>
```